Signage Design Project

Busisness is a bakery and deli long time owned by the Tavel family. Want to develop a new outside sign that communicates it is a deli and a bakery but keeps the tavel name in the design.

The sign when produced will be about 10' by 3' . It is not lighted at present but could be if it were advantageous.

The name of the store is:

Tavel's Harbor Lane Bakery and Deli. The concept is to have a new,modern sign that reinforces that it is a deli and a bakery, as most people only know about the bakery side of the business
Updates

The name Tavel is just a reinforcer so the people kno it is still in the family.  The emphasis should be on the HARBOR LANE BAKERY and DELI

Target Market(s)

Small business breakfast and lunch customers

Industry/Entity Type

Bakery

Requirements
Must have
• Great impact from the road. Communicate that it is a deli and a bakery. Keep the Tavel name but need not be a major design element

```html
<!DOCTYPE html>
<html lang="en">
<head>
<meta charset="utf-8">
<title>Tavel's Harbor Lane Bakery &amp; Deli — Sign</title>
<link rel="stylesheet" href="https://fonts.googleapis.com/css2?family=Righteous&display=swap">
<style>
  :root {
    --sign-glow: #921a4b;
    --sign-mid: #7a123c;
    --sign-edge: #4a0520;
    --letter: #ffffff;
    --letter-shadow: #0a0306;
  }
  html, body {
    margin: 0;
    padding: 0;
    width: 1200px;
    height: 360px;
    overflow: hidden;
  }
  .sign {
    display: block;
    width: 1200px;
    height: 360px;
    background: radial-gradient(ellipse 60% 95% at 50% 50%, var(--sign-glow) 0%, var(--sign-mid) 55%, var(--sign-edge) 100%);
  }
  .sign__text {
    font-family: "Righteous", "Arial Black", sans-serif;
    text-anchor: middle;
  }
  .sign__text--shadow { fill: var(--letter-shadow); }
  .sign__text--face { fill: var(--letter); }
  .sign__family { font-size: 66px; }
  .sign__trade { font-size: 170px; }
</style>
</head>
<body>
<svg class="sign" viewBox="0 0 1200 360" width="1200" height="360" role="img" aria-label="Tavel's Harbor Lane Bakery &amp; Deli">
  <g class="sign__family" aria-hidden="true">
    <text class="sign__text sign__text--shadow" x="576" y="122" textLength="650" lengthAdjust="spacingAndGlyphs">Tavel's Harbor Lane</text>
  </g>
  <text class="sign__text sign__text--face sign__family" x="580" y="118" textLength="650" lengthAdjust="spacingAndGlyphs">Tavel's Harbor Lane</text>

  <g class="sign__trade" aria-hidden="true">
    <text class="sign__text sign__text--shadow" x="594" y="305" textLength="1120" lengthAdjust="spacingAndGlyphs">Bakery &amp; Deli</text>
  </g>
  <text class="sign__text sign__text--face sign__trade" x="600" y="299" textLength="1120" lengthAdjust="spacingAndGlyphs">Bakery &amp; Deli</text>
</svg>
</body>
</html>
```